Ram and co fleecing works pty ltd

We are sheep shearing contractors,we are looking for a simple design business card, with a drawing like picture of a Australian sheep on it, then just standard details, name, phone, email, po box.
We would like double sided, with 2 lines of wiriting on the back, no bright colours please.
We like black and white, doesn't have to be too serious, however nothing to far left of cwntre.
On the back of the card we would like professional shearing contract offering full contract team.
Can use use the symbol & in the name instead of and.

Target Market(s)

Sheep farmers, target males from age 20 and up

Contact Information for Business Card

Company name ram and co fleecing works pty ltd
Marcus haldenby 0471305846, po box 4072 yarrowdale vic 3988,
Email ramandcofleecing@mailbarn.example, eastvale shearing contractor

Font styles to use
Serif

Colors

Designer to choose only greyscale colors for use in the design.

Requirements
Nice to have
• Simple design

```html
<!DOCTYPE html>
<html lang="en">
<head>
<meta charset="utf-8">
<title>Ram &amp; Co Fleecing Works — Business Card</title>
<link rel="stylesheet" href="https://fonts.googleapis.com/css2?family=Open+Sans:wght@400;600;700&display=swap">
<style>
  :root {
    --page: #e6e6e4;
    --card: #ffffff;
    --ink: #1c1c1c;
    --ink-soft: #4a4a4a;
    --rule: #2a2a2a;
    --dots: #9a9a9a;
    --art-dark: #8e8e8e;
    --art-light: #d6d6d6;
    --art-faint: #ececec;
  }
  * { box-sizing: border-box; margin: 0; padding: 0; }
  html, body {
    width: 1200px; height: 800px; overflow: hidden;
    background: var(--page);
    font-family: "Open Sans", Arial, sans-serif;
    color: var(--ink);
  }
  .sheet {
    width: 1200px; height: 800px;
    display: flex; align-items: center; justify-content: center; gap: 50px;
  }
  .card {
    position: relative;
    width: 520px; height: 300px;
    background: var(--card);
    box-shadow: 0 4px 14px rgba(0,0,0,.12);
    overflow: hidden;
  }

  /* Brand lockup */
  .brand { position: absolute; }
  .brand__name {
    font-weight: 700; font-size: 16px; letter-spacing: .02em;
    text-transform: uppercase; color: var(--ink); white-space: nowrap;
  }
  .brand__rule { height: 1px; background: var(--rule); margin-top: 6px; }

  /* Illustration placeholders */
  .art {
    position: absolute;
    border-radius: 46% 54% 40% 60% / 50% 45% 55% 50%;
  }
  .card--front .art {
    left: 40px; top: 70px; width: 200px; height: 200px;
    background: radial-gradient(circle at 45% 55%, var(--art-light), var(--art-dark));
  }
  .card--back .art {
    right: 30px; top: 40px; width: 140px; height: 170px;
    background: radial-gradient(circle at 50% 50%, var(--art-faint), var(--art-light));
    opacity: .8;
  }

  /* Front */
  .card--front .brand { right: 36px; top: 36px; text-align: right; }
  .person {
    position: absolute; left: 270px; top: 118px;
    font-size: 17px; font-weight: 400; color: var(--ink);
  }
  .contacts { position: absolute; left: 270px; top: 158px; list-style: none; }
  .contacts li {
    display: flex; align-items: center; gap: 8px;
    font-size: 11px; line-height: 1.25; color: var(--ink-soft);
    margin-bottom: 8px;
  }
  .contacts .icon {
    flex: none; width: 14px; height: 14px;
    background: var(--ink); border-radius: 3px;
    display: flex; align-items: center; justify-content: center;
  }

  /* Back */
  .card--back .brand { left: 36px; top: 120px; }
  .card--back .brand__name { font-size: 15px; }
  .lines { position: absolute; left: 250px; top: 40px; }
  .tagline { position: absolute; right: 30px; bottom: 22px; text-align: right; }
  .tagline__lead { font-size: 11px; color: var(--ink-soft); }
  .tagline__main {
    font-size: 11.5px; color: var(--ink); margin-top: 3px;
    border-top: 1px solid var(--rule); padding-top: 4px;
  }
</style>
</head>
<body>
<main class="sheet">

  <section class="card card--front" aria-label="Card front">
    <div class="art" role="img" aria-label="Greyscale drawing of a shearer holding an Australian merino sheep"></div>

    <div class="brand">
      <p class="brand__name">Ram &amp; Co Fleecing Works Pty Ltd</p>
      <div class="brand__rule"></div>
    </div>

    <p class="person">Marcus haldenby</p>

    <ul class="contacts">
      <li>
        <span class="icon">
          <svg width="9" height="9" viewBox="0 0 24 24" fill="#fff"><path d="M6.6 10.8a15 15 0 0 0 6.6 6.6l2.2-2.2a1 1 0 0 1 1-.25 11.4 11.4 0 0 0 3.6.57 1 1 0 0 1 1 1V20a1 1 0 0 1-1 1A17 17 0 0 1 3 4a1 1 0 0 1 1-1h3.5a1 1 0 0 1 1 1c0 1.25.2 2.45.57 3.6a1 1 0 0 1-.25 1z"/></svg>
        </span>
        0471305846
      </li>
      <li>
        <span class="icon">
          <svg width="9" height="9" viewBox="0 0 24 24" fill="none" stroke="#fff" stroke-width="2.5"><rect x="2" y="5" width="20" height="14"/><path d="M2 6l10 7 10-7"/></svg>
        </span>
        <span>ramandcofleecing@mailbarn.example,<br>eastvale shearing contractor</span>
      </li>
      <li>
        <span class="icon">
          <svg width="9" height="9" viewBox="0 0 24 24" fill="#fff"><path d="M12 2a7 7 0 0 0-7 7c0 5 7 13 7 13s7-8 7-13a7 7 0 0 0-7-7zm0 9.5A2.5 2.5 0 1 1 12 6.5a2.5 2.5 0 0 1 0 5z"/></svg>
        </span>
        po box 4072 yarrowdale vic 3988,
      </li>
    </ul>
  </section>

  <section class="card card--back" aria-label="Card back">
    <div class="art" role="img" aria-label="Faint greyscale drawing of a shearer with a sheep"></div>

    <div class="brand">
      <p class="brand__name">Ram &amp; Co Fleecing Works Pty Ltd</p>
      <div class="brand__rule"></div>
    </div>

    <svg class="lines" width="250" height="180" viewBox="0 0 250 180" aria-hidden="true">
      <line x1="0" y1="10" x2="240" y2="10" stroke="var(--dots)" stroke-width="1" stroke-dasharray="2 3"/>
      <line x1="0" y1="175" x2="240" y2="175" stroke="var(--dots)" stroke-width="1" stroke-dasharray="2 3"/>
    </svg>

    <div class="tagline">
      <p class="tagline__lead">we would like</p>
      <p class="tagline__main">professional shearing contract offering full contract team</p>
    </div>
  </section>

</main>
</body>
</html>
```